Web Page Design for a Website that Provides Tutoring

I am looking to create an online tutoring website. The website will allow parents or students to contact tutors with a view to instructing them to tutor themselves or their children.

The name of the website is LendYourLessons.

This brief is to create the design for one of the web pages for this web site. I am hoping the same designer will be available to design other pages.

The page I want designed is one of the more complex and I have attached the design as an excel spreadsheet. The web page needs to include all the items on this page but if you want to change the positioning of the items then Im fine with that.

I recently had two logos created for this website. My favourite is the one with a mortar board but im not sure I like the colours. I have attached both of these logos and you can use either of them, change the colours or create something different. I just want a design pleasing to the eye. If the logo is changed I would like that in a seperate file.

So can you please submit designs for this page. I have attached the two logos which you can use, change or if you feel you have a better idea then you can use that.

On the spreadsheet the Send Message, Favourite etc are buttons.

Target Market(s)

People who want to better themselves.
Possible middle class to upper class.

Industry/Entity Type

Tutoring

Number of Pages Required

1 page

Requirements
Must have
• The designs must have alot of the information attached in the spreadsheet.

```html
<!DOCTYPE html>
<html lang="en">
<head>
<meta charset="utf-8">
<title>LendYourLessons – Tutor Profile</title>
<link rel="stylesheet" href="https://fonts.googleapis.com/css2?family=Open+Sans:wght@300;400;600;700&family=Oswald:wght@500&family=Cabin+Sketch:wght@700&display=swap">
<style>
:root{
  --navy:#25273c;
  --footer:#1f1f24;
  --orange:#f47a1f;
  --orange-dark:#e0600e;
  --yellow:#f0b300;
  --green:#2fa880;
  --green-dark:#248a68;
  --purple:#565691;
  --purple-dark:#3f3f75;
  --star:#f5b21b;
  --text:#444;
  --muted:#777;
  --line:#e2e2e2;
  --avail:#d9fad9;
  --taken:#f2673f;
  --reserved:#f5961d;
  --no:#2f5c9a;
  --red:#e0161f;
}
*{box-sizing:border-box;margin:0;padding:0}
html,body{width:1200px;height:2365px;overflow:hidden}
body{position:relative;background:#fff;font-family:"Open Sans",Arial,sans-serif;color:var(--text);font-size:13px}
.abs{position:absolute}
svg{display:block}

/* header */
.site-header{left:0;top:0;width:1200px;height:73px;background:var(--navy)}
.brand{left:74px;top:20px;display:flex;align-items:center;gap:8px;color:var(--orange);font-weight:700;font-size:27px;letter-spacing:-.5px}
.brand-mark{width:16px;height:16px;background:var(--orange);border-radius:3px}
.main-nav{top:29px;left:0;width:1200px;height:20px}
.main-nav a{position:absolute;color:#fff;font-size:13px;text-decoration:none}
.main-nav a.active::after{content:"";position:absolute;left:-2px;right:-2px;top:23px;height:2px;background:var(--orange)}
.account{left:993px;top:28px;color:#fff;font-size:13px;display:flex;gap:7px;align-items:center}

/* hero */
.hero{left:0;top:73px;width:1200px;height:480px;background:linear-gradient(90deg,#eef0f2 0%,#f6f7f8 45%,#fff 60%)}
.hero-photo{left:0;top:73px;width:678px;height:480px;background:linear-gradient(120deg,#e6e8ea 0%,#f2f2f2 35%,#3d4356 52%,#2e3346 70%,#f4f4f4 90%)}
.hi-bubble{left:599px;top:160px;width:106px;height:106px;border-radius:50%;background:var(--orange);color:#fff;font-family:Georgia,serif;font-size:48px;display:flex;align-items:center;justify-content:center}
.hi-tail{left:608px;top:248px}
.hero-title{left:719px;top:172px;font-family:"Cabin Sketch",cursive;color:#3fae8a;font-size:50px;white-space:nowrap}
.hero-sub{left:719px;top:238px;font-weight:300;font-size:38px;color:#444}
.hero-text{left:720px;top:295px;width:400px;font-size:13.5px;line-height:21px;color:#555}
.btn{display:flex;align-items:center;justify-content:center;gap:8px;color:#fff;font-weight:700;font-size:12px;border-radius:2px;text-transform:uppercase}
.btn-register{left:721px;top:393px;width:154px;height:31px;background:var(--orange);box-shadow:0 2px 0 var(--orange-dark)}
.btn-demo{left:885px;top:393px;width:165px;height:31px;background:var(--green);box-shadow:0 2px 0 var(--green-dark)}

/* panels */
.panel{top:553px;height:311px;width:400px}
.panel-contact{left:0;background:var(--yellow)}
.panel-schedule{left:400px;background:var(--green)}
.panel-reviews{left:800px;background:var(--purple)}
.panel-title{font-family:"Oswald",sans-serif;color:#fff;font-size:27px;text-transform:uppercase;letter-spacing:-.3px}
.field{background:#fff;border-radius:2px;color:#999;font-size:12px;padding:9px 12px}
.panel-btn{height:47px;font-size:14px;border-radius:2px}
.tick-list{list-style:none;color:#fff;font-size:13px}
.tick-list li{display:flex;align-items:center;gap:10px;height:32px}
.rating-row{display:flex;align-items:center;gap:10px;color:#fff;font-size:11px;height:18px}
.rating-row .lbl{width:30px}
.bar{width:92px;height:7px;background:#fff}
.bar.full{background:var(--star)}

/* stats */
.stats{font-size:12.5px;color:#555}
.stat-row{position:absolute;left:0;display:flex;align-items:center;height:36px;border-bottom:1px solid var(--line)}
.stars{color:var(--star);letter-spacing:1px;font-size:15px}
.stars .off{color:#ccc}
.feedback{background:var(--red);color:#fff;font-size:12px;font-weight:600;padding:3px 10px;border-radius:2px;display:flex;gap:6px;align-items:center}
.info-head{font-weight:700;color:#333}

/* subject table */
.subjects{left:73px;top:1074px;width:1053px}
.block-head{height:36px;background:var(--orange);color:#fff;font-weight:700;font-size:16px;display:flex;align-items:center;padding:0 14px;justify-content:space-between}
table{width:100%;border-collapse:collapse;font-size:12.5px}
th{background:#e7e7e7;font-weight:400;color:#555;height:40px;text-align:left}
td{height:36.6px;border-top:1px solid #fff;color:#555}
tbody tr:nth-child(odd){background:#f3f3f3}
tbody tr:nth-child(even){background:#f8f8f8}

/* availability */
.availability{left:73px;top:1410px;width:1053px;height:309px;border:1px solid var(--line);border-top:none}
.avail-grid{display:grid;grid-template-columns:131px repeat(7,1fr);grid-template-rows:52px repeat(3,53px);gap:1px;background:#fff;font-size:12.5px;color:#555}
.avail-grid div{display:flex;align-items:center;justify-content:center;background:var(--avail)}
.avail-grid .hd{background:#e7e7e7}
.avail-grid .tm{background:#eeeeee}
.avail-grid .taken{background:var(--taken)}
.avail-grid .reserved{background:var(--reserved)}
.avail-grid .no{background:var(--no)}
.legend{display:flex;justify-content:center;gap:22px;margin-top:20px;font-size:12.5px;color:#555}
.legend span{display:flex;align-items:center;gap:8px}
.legend i{width:15px;height:15px;display:block}
.month{display:flex;align-items:center;gap:12px;font-size:17px}

/* reviews */
.section-title{left:0;width:1200px;top:1772px;text-align:center;font-size:19px;font-weight:600;color:#333}
.title-rule{left:584px;top:1810px;width:32px;height:3px;background:var(--orange)}
.review{top:1858px;width:335px}
.avatar{width:76px;height:76px;border:1px solid #ddd}
.review-name{position:absolute;left:92px;top:2px;font-weight:700;font-size:14px;color:#333}
.review-stars{position:absolute;left:92px;top:30px}
.review-note{position:absolute;left:92px;top:55px;font-size:10px;color:#888}
.review-quote{margin-top:19px;font-size:12.5px;line-height:20px;color:#555}

/* footer */
.site-footer{left:0;top:2039px;width:1200px;height:326px;background:var(--footer);color:#888;font-size:12.5px}
.foot-col{position:absolute;top:38px;line-height:26px}
.foot-col h4{color:#fff;font-size:13px;font-weight:700;margin-bottom:8px;line-height:20px}
.foot-input{width:243px;border-bottom:1px solid #666;height:30px;margin-top:6px;line-height:34px}
.foot-submit{width:243px;height:35px;background:var(--green);color:#fff;font-weight:700;font-size:12px;display:flex;align-items:center;justify-content:center;margin-top:20px}
.social{display:flex;gap:7px;margin-top:24px}
.social i{width:34px;height:34px;border-radius:50%;display:block}
.copyright{position:absolute;left:434px;top:276px;font-size:12px;color:#777}
</style>
</head>
<body>

<header class="abs site-header"></header>
<div class="abs brand"><span class="brand-mark"></span>LendYourLessons</div>
<nav class="abs main-nav">
  <a class="active" style="left:404px">Home</a>
  <a style="left:470px">Search</a>
  <a style="left:542px">Student</a>
  <a style="left:620px">Tutor</a>
  <a style="left:681px">About</a>
  <a style="left:749px">Contact</a>
</nav>
<div class="abs account">
  <svg width="14" height="14" viewBox="0 0 14 14"><circle cx="7" cy="4" r="3.3" fill="#f47a1f"/><path d="M1 14c0-4 2.6-6 6-6s6 2 6 6z" fill="#f47a1f"/></svg>
  <span>Login &nbsp;or&nbsp; Register</span>
</div>

<section class="abs hero"></section>
<div class="abs hero-photo" role="img" aria-label="Photo of a smiling tutor in a navy suit standing beside a whiteboard"></div>
<div class="abs hi-bubble">Hi.</div>
<svg class="abs hi-tail" width="30" height="28" viewBox="0 0 30 28"><path d="M8 0 L0 28 L28 8z" fill="#f47a1f"/></svg>
<h1 class="abs hero-title">My name is Marla</h1>
<p class="abs hero-sub">I am....</p>
<p class="abs hero-text">Passionate about teaching. I find it easy to inspire children to want learn, a gift not many people have. I am excellent English Teachear and Understand the letest teaching practices.</p>
<div class="abs btn btn-register">
  <svg width="12" height="12" viewBox="0 0 12 12"><path d="M0 12l1-3.5 7-7 2.5 2.5-7 7z" fill="#fff"/></svg>Register Today</div>
<div class="abs btn btn-demo">
  <svg width="14" height="10" viewBox="0 0 14 10"><rect width="9" height="10" rx="1" fill="#fff"/><path d="M9 5l5-4v8z" fill="#fff"/></svg>Watch Our Demo</div>

<section class="abs panel panel-contact">
  <h2 class="abs panel-title" style="left:73px;top:26px">Contact Tutor</h2>
  <div class="abs field" style="left:73px;top:81px;width:255px;height:35px">Subject</div>
  <div class="abs field" style="left:73px;top:127px;width:255px;height:101px">Enter Your Messages</div>
  <div class="abs btn panel-btn" style="left:73px;top:239px;width:255px;background:var(--orange);box-shadow:0 2px 0 var(--orange-dark)">
    <svg width="20" height="14" viewBox="0 0 20 14"><rect x="4" y="1" width="16" height="12" fill="#fff"/><path d="M4 1l8 7 8-7" stroke="#f47a1f" stroke-width="1.5" fill="none"/><path d="M0 5h3M1 9h3" stroke="#fff" stroke-width="1.5"/></svg>Send Message</div>
</section>

<section class="abs panel panel-schedule">
  <p class="abs" style="left:72px;top:26px;width:240px;color:#fff;font-weight:700;font-size:14px;line-height:21px">She Would like to know your schedule.</p>
  <ul class="abs tick-list" style="left:72px;top:85px">
    <li><svg width="14" height="14" viewBox="0 0 14 14"><circle cx="7" cy="7" r="6" stroke="#fff" stroke-width="1.4" fill="none"/><path d="M4 7l2.2 2.2L10.5 4.5" stroke="#fff" stroke-width="1.6" fill="none"/></svg>Offline Lessons</li>
    <li><svg width="14" height="14" viewBox="0 0 14 14"><circle cx="7" cy="7" r="6" stroke="#fff" stroke-width="1.4" fill="none"/><path d="M4 7l2.2 2.2L10.5 4.5" stroke="#fff" stroke-width="1.6" fill="none"/></svg>Affordable Rates</li>
    <li><svg width="14" height="14" viewBox="0 0 14 14"><circle cx="7" cy="7" r="6" stroke="#fff" stroke-width="1.4" fill="none"/><path d="M4 7l2.2 2.2L10.5 4.5" stroke="#fff" stroke-width="1.6" fill="none"/></svg>1-on-1 Tutoring</li>
    <li><svg width="14" height="14" viewBox="0 0 14 14"><circle cx="7" cy="7" r="6" stroke="#fff" stroke-width="1.4" fill="none"/><path d="M4 7l2.2 2.2L10.5 4.5" stroke="#fff" stroke-width="1.6" fill="none"/></svg>Refund Policy</li>
  </ul>
  <div class="abs btn panel-btn" style="left:67px;top:239px;width:255px;background:var(--green-dark);box-shadow:0 2px 0 #1d6f54">
    <svg width="14" height="16" viewBox="0 0 14 16"><path d="M7 0l2 5h-4zM5 6h4v5l4 5H1l4-5z" fill="#fff"/></svg>Contact Favor</div>
</section>

<section class="abs panel panel-reviews">
  <h2 class="abs panel-title" style="left:69px;top:26px">Customer Reviews</h2>
  <div class="abs" style="left:69px;top:78px;display:flex;align-items:center;gap:8px;color:#fff;font-size:11px"><span class="stars">★★★★★</span>15 (5.0 out of 5 stars)</div>
  <div class="abs" style="left:69px;top:105px">
    <div class="rating-row"><span class="lbl">5 Star</span><span class="bar full"></span>100%</div>
    <div class="rating-row"><span class="lbl">4 Star</span><span class="bar"></span>0%</div>
    <div class="rating-row"><span class="lbl">3 Star</span><span class="bar"></span>0%</div>
    <div class="rating-row"><span class="lbl">2 Star</span><span class="bar"></span>0%</div>
    <div class="rating-row"><span class="lbl">1 Star</span><span class="bar"></span>0%</div>
  </div>
  <p class="abs" style="left:69px;top:204px;color:#fff;font-size:12.5px">Share your thoughts with other customers</p>
  <div class="abs btn panel-btn" style="left:70px;top:239px;width:256px;background:var(--purple-dark);box-shadow:0 2px 0 #2f2f5c">
    <svg width="14" height="14" viewBox="0 0 12 12"><path d="M0 12l1-3.5 7-7 2.5 2.5-7 7z" fill="#fff"/></svg>Write A Review</div>
</section>

<section class="abs stats" style="left:73px;top:917px;width:1053px;height:135px">
  <div class="stat-row" style="top:0;width:500px"><span style="width:132px">Review Score</span><span class="stars" style="width:95px">★★★★<span class="off">★</span></span><span style="width:134px">4.5/5</span><span>Member Since</span></div>
  <div class="stat-row" style="top:36px;width:500px"><span style="width:132px">Reliability</span><span class="stars" style="width:95px">★★★★<span class="off">★</span></span><span style="width:134px">4.0/5.0</span><span>Last Logged In</span></div>
  <div class="stat-row" style="top:72px;width:500px"><span style="width:132px">Punctuality</span><span class="stars" style="width:95px">★★★★<span class="off">★</span></span><span style="width:134px">4.6/5</span><span class="feedback"><svg width="11" height="11" viewBox="0 0 11 11"><path d="M0 5l11-5-4 11-2-4z" fill="#fff"/></svg>Leave Feedback</span></div>
  <div class="abs" style="left:528px;top:0;width:1px;height:132px;background:var(--line)"></div>
  <div class="stat-row" style="top:0;left:555px;width:498px"><span class="info-head" style="width:181px">Tutoring Type</span><span class="info-head" style="width:178px">In Personal Only</span><span class="info-head">Teacher</span></div>
  <div class="stat-row" style="top:36px;left:555px;width:498px"><span style="width:181px">Willing To Travel</span><span style="width:178px">Home Only</span><span>Full Time Tutor</span></div>
  <div class="stat-row" style="top:72px;left:555px;width:498px"><span style="width:181px">Age</span><span style="width:178px">20</span><span>Full Time Student</span></div>
  <div class="stat-row" style="top:108px;left:555px;width:498px;border-bottom:none"><span>DBS (CRB)</span></div>
</section>

<section class="abs subjects">
  <div class="block-head">Subject Taught</div>
  <table>
    <colgroup><col style="width:208px"><col style="width:140px"><col style="width:155px"><col style="width:123px"><col style="width:138px"><col style="width:153px"><col></colgroup>
    <thead><tr><th></th><th>Primary</th><th>Secondary</th><th>GCSE</th><th>A-LEVEL</th><th>University</th><th>Adult Learner</th></tr></thead>
    <tbody>
      <tr><td style="padding-left:28px">Biology</td><td>£20</td><td></td><td>£25</td><td>£30</td><td></td><td></td></tr>
      <tr><td style="padding-left:28px">Chemistry</td><td>£20</td><td></td><td>£25</td><td>£30</td><td></td><td></td></tr>
      <tr><td style="padding-left:28px">Chemistry</td><td>£20</td><td></td><td>£25</td><td>£30</td><td></td><td></td></tr>
      <tr><td style="padding-left:28px">Chemistry</td><td>£20</td><td></td><td>£25</td><td>£30</td><td></td><td></td></tr>
      <tr><td style="padding-left:28px">Chemistry</td><td>£20</td><td></td><td>£25</td><td>£30</td><td></td><td></td></tr>
    </tbody>
  </table>
</section>

<section class="abs availability">
  <div class="block-head" style="margin:0 -1px">Availability
    <span class="month">December 2016
      <svg width="8" height="12" viewBox="0 0 8 12"><path d="M7 1L2 6l5 5" stroke="#fff" stroke-width="1.6" fill="none"/></svg>
      <svg width="13" height="13" viewBox="0 0 13 13"><rect x="0.5" y="2" width="12" height="10.5" fill="none" stroke="#fff"/><rect x="0.5" y="2" width="12" height="3" fill="#fff"/><rect x="3" y="7" width="2" height="2" fill="#fff"/><rect x="7" y="7" width="2" height="2" fill="#fff"/></svg>
      <svg width="8" height="12" viewBox="0 0 8 12"><path d="M1 1l5 5-5 5" stroke="#fff" stroke-width="1.6" fill="none"/></svg>
    </span>
  </div>
  <div class="avail-grid">
    <div class="hd"></div><div class="hd">Mon (7th)</div><div class="hd">Tue (8th)</div><div class="hd">Wed (9th)</div><div class="hd">Thu (10th)</div><div class="hd">Fri (11th)</div><div class="hd">Sat (12th)</div><div class="hd">Sun (13th)</div>
    <div class="tm">7-8PM</div><div></div><div></div><div class="taken"></div><div></div><div></div><div></div><div></div>
    <div class="tm">8-9PM</div><div></div><div></div><div class="reserved"></div><div></div><div></div><div></div><div class="no"></div>
    <div class="tm">4-5PM</div><div></div><div></div><div class="no"></div><div></div><div class="reserved"></div><div></div><div></div>
  </div>
  <div class="legend">
    <span><i style="background:var(--avail)"></i>Available</span>
    <span><i style="background:var(--taken)"></i>Taken</span>
    <span><i style="background:var(--reserved)"></i>Reserved</span>
    <span><i style="background:var(--no)"></i>No</span>
  </div>
</section>

<h2 class="abs section-title">Tutors Reviews</h2>
<div class="abs title-rule"></div>

<article class="abs review" style="left:73px">
  <div class="avatar" role="img" aria-label="Portrait photo of reviewer Janelle" style="background:linear-gradient(#e9e3dc,#d2b89c)"></div>
  <span class="review-name">Janelle</span>
  <span class="review-stars stars">★★★<span class="off">★★</span></span>
  <span class="review-note">(Star Rateing 3)</span>
  <p class="review-quote">" Reference site about Lorem Ipsum, giving information on its origins, as well as a random Lipsum generator."</p>
</article>
<article class="abs review" style="left:434px">
  <div class="avatar" role="img" aria-label="Portrait photo of reviewer Tom Weller" style="background:linear-gradient(#e4e6ea,#6b6f7a)"></div>
  <span class="review-name">Tom Weller</span>
  <span class="review-stars stars">★★★★<span class="off">★</span></span>
  <span class="review-note">(Star Rateing 4)</span>
  <p class="review-quote">" Reference site about Lorem Ipsum, giving information on its origins, as well as a random Lipsum generator."</p>
</article>
<article class="abs review" style="left:793px">
  <div class="avatar" role="img" aria-label="Portrait photo of reviewer Sorrel" style="background:linear-gradient(#e8e2de,#5a4036)"></div>
  <span class="review-name">Sorrel</span>
  <span class="review-stars stars">★★★<span class="off">★★</span></span>
  <span class="review-note">(Star Rateing 3)</span>
  <p class="review-quote">" Reference site about Lorem Ipsum, giving information on its origins, as well as a random Lipsum generator."</p>
</article>

<footer class="abs site-footer">
  <div class="foot-col" style="left:73px;width:250px">
    <h4>Get Our Newsletter</h4>
    <p style="line-height:20px">To receive updates about my tutor, Join our newsletter.</p>
    <div class="foot-input">Name</div>
    <div class="foot-input">Email</div>
    <div class="foot-submit">SUBMIT</div>
  </div>
  <div class="foot-col" style="left:434px">
    <h4>Contact Us</h4>
    <p style="line-height:20px">228 Lorem Ipsum dolor,<br>Dosis amet, -85485</p>
    <p style="line-height:20px;margin-top:16px">T: 1800 555 010<br>E: info@lendyourlessons.com</p>
    <div class="social"><i style="background:#3b5a9a"></i><i style="background:#2ba3e0"></i><i style="background:#d9412f"></i></div>
  </div>
  <div class="foot-col" style="left:705px">
    <h4>Quick Links</h4>
    <p>Home<br>Search<br>Student<br>Tutor<br>About<br>Contact</p>
  </div>
  <div class="foot-col" style="left:885px">
    <h4>Info Links</h4>
    <p>Register as a Student<br>Register as a Paretnt<br>Register as a Tutor</p>
  </div>
  <p class="copyright">Copyright 2016 Lend Your Lessons. All Rights Reserved.</p>
</footer>

</body>
</html>
```